Working Capital graphics

Our business advisory firm requires 9 images to be re-created and improved in the branding of our business.

The 9 images have been uploaded below and the colours and branding of the business can be found at the website www.tallowmereadvisory.com.au

```html
<!DOCTYPE html>
<html lang="en">
<head>
<meta charset="utf-8">
<title>Working Capital</title>
<link rel="stylesheet" href="https://fonts.googleapis.com/css2?family=Jost:wght@500;600&display=swap">
<style>
  :root {
    --navy: #14387f;
    --sky: #0cb0f2;
    --orange: #f7941d;
    --white: #ffffff;
    --label: #1b3a88;
  }
  html, body {
    margin: 0;
    padding: 0;
    width: 1200px;
    height: 1176px;
    overflow: hidden;
    background: var(--white);
  }
  .diagram {
    display: block;
    width: 1200px;
    height: 1176px;
  }
  .connector { stroke: var(--navy); stroke-width: 11; }
  .hub-ring { fill: var(--white); stroke: var(--navy); stroke-width: 13; }
  .hub-core { fill: var(--sky); }
  .hub-title {
    font-family: "Jost", "Futura", sans-serif;
    font-weight: 600;
    font-size: 104px;
    fill: var(--white);
    text-anchor: middle;
    letter-spacing: 1px;
  }
  .node-fill { fill: var(--white); }
  .node-arc { fill: none; stroke-width: 13; }
  .node-arc--warm { stroke: var(--orange); }
  .node-arc--cool { stroke: var(--sky); }
  .node-label {
    font-family: "Jost", "Futura", sans-serif;
    font-weight: 600;
    font-size: 37px;
    fill: var(--label);
    text-anchor: middle;
    letter-spacing: 0.5px;
  }
  .node-label--compact { font-size: 33px; }
</style>
</head>
<body>
<svg class="diagram" viewBox="0 0 1920 1882" xmlns="http://www.w3.org/2000/svg" role="img" aria-label="Working capital and its nine drivers">
  <defs>
    <g id="node-ring">
      <circle class="node-fill" r="155"/>
      <path class="node-arc node-arc--warm" d="M0,-155 A155,155 0 0 0 0,155"/>
      <path class="node-arc node-arc--cool" d="M0,-155 A155,155 0 0 1 0,155"/>
    </g>
  </defs>

  <!-- connectors -->
  <g class="connectors">
    <line class="connector" x1="957" y1="957" x2="957" y2="370"/>
    <line class="connector" x1="957" y1="957" x2="1337" y2="505"/>
    <line class="connector" x1="957" y1="957" x2="1541" y2="855"/>
    <line class="connector" x1="957" y1="957" x2="1473" y2="1250"/>
    <line class="connector" x1="957" y1="957" x2="1164" y2="1508"/>
    <line class="connector" x1="957" y1="957" x2="759" y2="1508"/>
    <line class="connector" x1="957" y1="957" x2="445" y2="1250"/>
    <line class="connector" x1="957" y1="957" x2="376" y2="857"/>
    <line class="connector" x1="957" y1="957" x2="577" y2="508"/>
  </g>

  <!-- hub -->
  <g class="hub">
    <circle class="hub-ring" cx="957" cy="957" r="343"/>
    <circle class="hub-core" cx="957" cy="957" r="302"/>
    <text class="hub-title" x="957" y="957">WORKING</text>
    <text class="hub-title" x="957" y="1053">CAPITAL</text>
  </g>

  <!-- nodes -->
  <g class="node" transform="translate(957 370)">
    <use href="#node-ring"/>
    <text class="node-label" y="-28">SUPPLY</text>
    <text class="node-label" y="16">CHAIN</text>
    <text class="node-label" y="60">ISSUES</text>
  </g>
  <g class="node" transform="translate(1337 505)">
    <use href="#node-ring"/>
    <text class="node-label" y="4">PROCESS</text>
    <text class="node-label" y="48">ISSUES</text>
  </g>
  <g class="node" transform="translate(1541 855)">
    <use href="#node-ring"/>
    <text class="node-label node-label--compact" y="-11">FORECASTING</text>
    <text class="node-label node-label--compact" y="27">AND PLANNING</text>
  </g>
  <g class="node" transform="translate(1473 1250)">
    <use href="#node-ring"/>
    <text class="node-label" y="-14">CUSTOMER</text>
    <text class="node-label" y="30">MANAGEMENT</text>
  </g>
  <g class="node" transform="translate(1164 1508)">
    <use href="#node-ring"/>
    <text class="node-label" y="-16">SKU</text>
    <text class="node-label" y="28">COMPLEXITY</text>
  </g>
  <g class="node" transform="translate(759 1508)">
    <use href="#node-ring"/>
    <text class="node-label" y="-16">SUPPLIER</text>
    <text class="node-label" y="28">MANAGEMENT</text>
  </g>
  <g class="node" transform="translate(445 1250)">
    <use href="#node-ring"/>
    <text class="node-label" y="-1">KPIS AND</text>
    <text class="node-label" y="43">MEASURES</text>
  </g>
  <g class="node" transform="translate(376 857)">
    <use href="#node-ring"/>
    <text class="node-label" y="-34">IT SYSTEMS</text>
    <text class="node-label" y="10">AND</text>
    <text class="node-label" y="54">INFORMATION</text>
  </g>
  <g class="node" transform="translate(577 508)">
    <use href="#node-ring"/>
    <text class="node-label" y="-1">TERMS AND</text>
    <text class="node-label" y="43">CONDITIONS</text>
  </g>
</svg>
</body>
</html>
```